Coastal Learner Bureau business cards

Australian company about to start offering its services. We recruit international students to come to study English, vocational education and postgraduate courses in Australia. We help them find the institution and select the right city they want to come to Australia. We are a young, online oriented and supportive agency. Our clients are between 18 and 35 years old, mainly University students, young professionals or people with work experience. We provide much more information that any other agency offer. We administrate a Facebook group with more than 11.000 members that daily ask questions about general information when coming to Australia, while they are here and even after they leave the country

Target Market(s)

International students from South America, Central America and Europe

Industry/Entity Type

Student

Contact Information for Business Card

Tomas Bilbrea
Managing Director
tomas@kelvarin.com.au
www.kelvoria.com.au
+61 491058264
Melbourne, Australia

Font styles to use
Serif
Sans Serif

Colors

Designer to choose colors to be used in the design.

Requirements
Must have
• Horizontal design
• Standard business card size and shape. If font uses green or yellow colours, they will have to match the ones from the logo
Nice to have
• UPDATE: Use the contents of the green image to design one of the card sides. Use our logo in the background of that side as watermark.
• Passport image, or immigration stamps. A picture of the Yarra River (from Melbourne) would be cool as well.
Should not have
• Non-standard business card size and shape
• Not black as the background colour of any sides as we are not a VIP agency or a hight class service. We are orientes to young people and they like colours, pictures, something attractive.
• Vertical design
• NO YELLOW or BLACK AS THE BACKGROUND COLOUR OF ANY SIDE OF THE BIZ CARD

```html
<!DOCTYPE html>
<html lang="en">
<head>
<meta charset="utf-8">
<title>Coastal Learner Bureau business cards</title>
<link rel="stylesheet" href="https://fonts.googleapis.com/css2?family=Arimo:wght@400;700&display=swap">
<style>
  :root {
    --stage: #2e2e2e;
    --green: #0d5e3a;
    --green-deep: #084d2f;
    --gold: #d4a814;
    --gold-text: #e2b81c;
    --white: #ffffff;
    --paper: #f4f4f2;
    --ink-green: #0b5a36;
  }
  * { box-sizing: border-box; margin: 0; padding: 0; }
  html, body {
    width: 1200px; height: 997px; overflow: hidden;
    background: var(--stage);
    font-family: "Arimo", Arial, sans-serif;
  }
  .card {
    position: absolute; left: 290px;
    width: 620px; height: 354px;
    box-shadow: 0 14px 30px rgba(0,0,0,.45);
    overflow: hidden;
  }
  /* Front */
  .card-front { top: 95px; background: var(--green); }
  .front-logo {
    position: absolute; left: 0; right: 0; top: 95px;
    text-align: center;
  }
  .brand-name {
    font-weight: 700; font-size: 64px; letter-spacing: 1px;
    color: var(--white);
  }
  .tagline {
    position: absolute; left: 0; right: 0; top: 262px;
    text-align: center; color: var(--white);
    font-weight: 700; font-size: 17px; letter-spacing: .5px;
  }
  .stripe-pair {
    position: absolute; left: 0; right: 0; top: 298px; height: 14px;
    border-top: 3px solid var(--gold); border-bottom: 3px solid var(--gold);
  }
  /* Back */
  .card-back { top: 520px; background: var(--paper); }
  .back-panel {
    position: absolute; left: 0; top: 0; bottom: 0; width: 330px;
    background: var(--green-deep);
  }
  .back-stripes {
    position: absolute; top: 0; bottom: 0; left: 330px; width: 22px;
    border-left: 5px solid var(--gold); border-right: 5px solid var(--gold);
    background: var(--green-deep);
  }
  .holder { position: absolute; left: 30px; top: 86px; }
  .holder-name { color: var(--white); font-weight: 700; font-size: 15px; letter-spacing: .3px; }
  .holder-role { color: var(--gold-text); font-size: 13px; margin-top: 3px; }
  .office { position: absolute; left: 30px; top: 160px; color: var(--white); font-size: 13px; line-height: 1.4; }
  .office-name { color: var(--gold-text); font-weight: 700; font-size: 15px; margin-bottom: 3px; }
  .contacts { position: absolute; left: 30px; top: 252px; list-style: none; }
  .contacts li {
    display: flex; align-items: center; gap: 9px;
    color: var(--white); font-size: 13px; height: 24px;
  }
  .contact-icon { width: 17px; height: 17px; flex: none; }
  .back-logo {
    position: absolute; left: 352px; right: 0; top: 110px; text-align: center;
  }
  .back-logo .brand-name { color: var(--ink-green); font-size: 54px; }
  .website {
    position: absolute; left: 352px; right: 0; top: 282px; text-align: center;
    color: var(--ink-green); font-weight: 700; font-size: 16px; letter-spacing: 1px;
  }
</style>
</head>
<body>
  <section class="card card-front" aria-label="Card front">
    <div class="front-logo"><span class="brand-name">Kelvoria</span></div>
    <p class="tagline">Hacemos más por ti!</p>
    <div class="stripe-pair"></div>
  </section>

  <section class="card card-back" aria-label="Card back">
    <div class="back-panel">
      <div class="holder">
        <p class="holder-name">TOMAS BILBREA</p>
        <p class="holder-role">Managing Director</p>
      </div>
      <div class="office">
        <p class="office-name">KELVORIA</p>
        <p>240 Harbour Lane, Suite 12</p>
        <p>Docklands, VIC 3008</p>
      </div>
      <ul class="contacts">
        <li>
          <svg class="contact-icon" viewBox="0 0 20 20"><circle cx="10" cy="10" r="10" fill="#d4a814"/></svg>
          kelvoria
        </li>
        <li>
          <svg class="contact-icon" viewBox="0 0 20 20"><circle cx="10" cy="10" r="10" fill="#d4a814"/><path d="M6.5 5.5l2 0 1 2.5-1.3 1a6 6 0 0 0 3 3l1-1.3 2.5 1v2a1.5 1.5 0 0 1-1.6 1.4A9 9 0 0 1 5 7.1 1.5 1.5 0 0 1 6.5 5.5z" fill="#084d2f"/></svg>
          +61 491058264
        </li>
        <li>
          <svg class="contact-icon" viewBox="0 0 20 20"><circle cx="10" cy="10" r="10" fill="#d4a814"/><rect x="5" y="6.5" width="10" height="7" fill="#084d2f"/><path d="M5 6.5l5 4 5-4" fill="none" stroke="#d4a814" stroke-width="1.2"/></svg>
          tomas@kelvarin.com.au
        </li>
      </ul>
    </div>
    <div class="back-stripes"></div>
    <div class="back-logo"><span class="brand-name">Kelvoria</span></div>
    <p class="website">WWW.KELVORIA.COM.AU</p>
  </section>
</body>
</html>
```